Can you make our site AWESOME?

Hi Guys,

I am a co-founder of Tallow Crate Rentals Australia, the world's first e-commerce skip bin business.

We are looking to update our site before a launch into the UK in March.

Please help us by submitting your designs for the following pages:

- Home page (www.tallowcraterentals.example.au)
- About us (https://www.tallowcraterentals.example.au/pages/about-us
- Contact us (https://www.tallowcraterentals.example.au/pages/contact-us)
- Quick Quote / Pricing (https://www.tallowcraterentals.example.au/pages/free-instant-quote-skip-bin-hire)

NOTES:
- Design should be high-converting
- best designs will be fresh, modern, easy to read, distinctive and memorable
- please use our logo and video colours
- feel free to change logos, layout, images and anything else you feel can be improved
- the winning designer will potentially have the opportunity to re-design the other pages on our site
- brief is for design only

Any questions just ask.

Thanks,
Oliver

```html
<!DOCTYPE html>
<html lang="en">
<head>
<meta charset="utf-8">
<title>Tallow Crate Rentals Australia</title>
<link href="https://fonts.googleapis.com/css2?family=Poppins:wght@300;400;500;600;700&display=swap" rel="stylesheet">
<style>
:root{
  --navy:#262a63;
  --indigo:#5c5f9f;
  --indigo-dark:#4b4e8c;
  --green:#3a9d5a;
  --sky:#c3e6ee;
  --sky-soft:#e6f5f8;
  --mist:#f4f5f8;
  --ink:#3c3f55;
  --muted:#6a6d80;
  --card:#ffffff;
  --line:#e2e4ea;
  --footer:#343536;
  --footer-base:#242526;
}
*{box-sizing:border-box;margin:0;padding:0}
html,body{width:1200px;height:3742px;overflow:hidden}
body{font-family:"Poppins",sans-serif;color:var(--ink);background:#fff;position:relative}
.abs{position:absolute}
/* header */
.site-header{left:0;top:0;width:1200px;height:66px;background:#fff;z-index:3}
.brand{left:88px;top:16px;display:flex;align-items:center;gap:10px}
.brand-mark{width:30px;height:30px;background:var(--navy);border-radius:4px}
.brand-name{font-weight:700;font-size:17px;color:var(--navy);line-height:1.05;width:220px}
.main-nav{left:400px;top:26px;display:flex;gap:46px;font-size:12px;font-weight:500;color:var(--navy)}
.call-btn{left:920px;top:0;width:190px;height:30px;background:var(--indigo);color:#fff;font-size:12px;font-weight:600;border-radius:0 0 8px 8px;display:flex;align-items:center;justify-content:center}
.login{left:920px;top:40px;width:190px;text-align:center;font-size:11px;font-weight:600;color:var(--green)}
/* hero */
.hero{left:0;top:66px;width:1200px;height:640px;background:linear-gradient(180deg,var(--sky) 0%,var(--sky-soft) 55%,#fff 100%)}
.skyline{left:0;top:440px;width:1200px;height:250px;background:linear-gradient(180deg,rgba(160,195,215,.25),rgba(170,205,190,.45))}
.hero-title{left:0;top:178px;width:1200px;text-align:center;font-size:46px;font-weight:700;color:var(--navy)}
.hero-sub{left:0;top:252px;width:1200px;text-align:center;font-size:23px;color:var(--green)}
.quote-label{left:0;top:318px;width:1200px;text-align:center;font-size:15px;font-weight:600;color:var(--navy)}
.search{height:56px;display:flex;border-radius:28px;overflow:hidden;box-shadow:0 4px 14px rgba(40,50,90,.12)}
.search-input{flex:1;background:#fff;padding-left:28px;display:flex;align-items:center;font-size:15px;color:#8a8c99}
.search-btn{width:124px;background:var(--indigo);color:#fff;font-size:13px;font-weight:600;display:flex;align-items:center;justify-content:center;gap:8px}
.hero .search{position:absolute;left:320px;top:302px;width:560px}
.audience{left:165px;top:558px;display:flex;gap:18px}
.audience-card{width:160px;height:158px;background:var(--card);border-radius:6px;box-shadow:0 6px 18px rgba(40,50,90,.12);display:flex;flex-direction:column;align-items:center;justify-content:center;gap:22px;font-size:12px;font-weight:600;color:var(--navy);letter-spacing:.5px}
/* rating + video */
.rated{left:0;top:775px;width:1200px;text-align:center;font-size:30px;color:var(--navy);line-height:1.3}
.video{left:240px;top:882px;width:735px;height:393px;background:linear-gradient(180deg,#6f6fae 0%,#7b7bb8 60%,#5e8a57 100%);box-shadow:0 8px 20px rgba(0,0,0,.15)}
.play{left:572px;top:1040px;width:78px;height:78px;border-radius:50%;background:#fff;display:flex;align-items:center;justify-content:center}
/* steps */
.steps-band{left:0;top:1230px;width:1200px;height:612px;background:var(--mist);clip-path:path("M0 60 Q600 -40 1200 60 L1200 612 L0 612 Z")}
.section-title{left:0;width:1200px;text-align:center;font-size:32px;color:var(--navy)}
.steps{left:80px;top:1487px;display:flex;gap:22px}
.step{position:relative;width:334px;height:150px;background:#fff;border:1px solid var(--line);padding:18px 16px 0 92px}
.step svg{position:absolute;left:20px;top:26px}
.step-num{position:absolute;left:34px;top:92px;font-size:44px;color:#e4e5ea;font-weight:600}
.step h3{font-size:19px;font-weight:600;color:var(--navy);margin-bottom:6px;white-space:nowrap}
.step p{font-size:12px;line-height:1.6;color:var(--ink)}
.step p b{color:var(--navy)}
.step p span{color:var(--green)}
.manage{left:0;top:1740px;width:1200px;text-align:center;font-size:20px;color:var(--navy);line-height:1.4}
/* testimonials */
.reviews-band{left:0;top:1842px;width:1200px;height:700px;background:linear-gradient(180deg,var(--sky) 0%,#e9f6f9 50%,#fff 100%)}
.reviews{left:95px;top:2007px;display:flex;gap:26px}
.review{position:relative;width:324px;height:408px;background:#fff;box-shadow:0 6px 20px rgba(40,50,90,.08);padding:88px 54px 0 54px}
.quote-mark{position:absolute;left:36px;top:-14px;font-size:90px;line-height:1;color:#e9ebef;font-weight:700}
.review p{font-size:13px;line-height:2;color:var(--ink)}
.review hr{border:0;border-top:1px solid var(--line);margin:22px 0 18px}
.reviewer{display:flex;align-items:center;gap:14px;font-size:16px;color:var(--green)}
.avatar{width:36px;height:36px;border-radius:50%;background:#c9b7a4}
.dots{left:585px;top:2450px;display:flex;gap:6px}
.dots i{width:7px;height:7px;border-radius:50%;background:#c6c8d4}
.dots i:first-child{background:var(--indigo)}
/* benefits */
.benefits{left:60px;top:2672px;display:flex;width:1080px}
.benefit{width:270px;text-align:center;padding:0 22px}
.benefit svg{display:block;margin:0 auto 18px}
.benefit h4{font-size:15px;font-weight:600;color:var(--navy);margin-bottom:10px}
.benefit p{font-size:12.5px;line-height:1.75;color:var(--ink)}
/* cta */
.cta{left:0;top:2965px;width:1200px;height:440px;background:var(--indigo)}
.cta-city{left:0;top:3090px;width:1200px;height:280px;background:linear-gradient(180deg,rgba(80,82,140,0),rgba(70,72,128,.9))}
.cta-title{left:0;top:3025px;width:1200px;text-align:center;font-size:36px;font-weight:600;color:#fff}
.cta-sub{left:0;top:3085px;width:1200px;text-align:center;font-size:17px;color:#fff}
.cta-label{left:0;top:3132px;width:1200px;text-align:center;font-size:11px;font-weight:600;color:#fff;letter-spacing:.5px}
.cta .search{position:absolute;left:342px;top:201px;width:560px}
.cta .search-btn{background:var(--green)}
/* footer */
.footer{left:0;top:3270px;width:1200px;height:360px;background:var(--footer);clip-path:path("M0 80 C150 20 260 20 420 60 C560 95 640 100 780 55 C930 10 1050 10 1200 70 L1200 360 L0 360 Z")}
.foot-col{top:3404px;font-size:12px;line-height:2.2;color:#e7e7ea}
.news h5{font-size:12px;font-weight:500;color:#fff}
.news p{font-size:11px;line-height:1.6;color:#e0e0e4}
.subscribe{margin-top:16px;width:360px;height:42px;border-radius:21px;background:#fff;display:flex;overflow:hidden}
.subscribe span{flex:1;display:flex;align-items:center;padding-left:22px;font-size:12px;color:#555}
.subscribe b{width:128px;background:var(--green);color:#fff;font-size:12px;font-weight:600;display:flex;align-items:center;justify-content:center;border-radius:21px}
.social{display:flex;gap:26px;margin-top:16px}
.social i{width:16px;height:16px;border-radius:50%;border:2px solid #d8d8dc}
.base{left:0;top:3628px;width:1200px;height:114px;background:var(--footer-base)}
.copyright{left:95px;top:3640px;font-size:11px;color:#d8d8dc}
.pay{left:842px;top:3636px;display:flex;gap:14px}
.pay i{width:38px;height:24px;border-radius:3px;background:#5a5b5e}
</style>
</head>
<body>

<header class="site-header abs">
  <div class="brand abs"><span class="brand-mark"></span><span class="brand-name">TALLOW CRATE RENTALS AUSTRALIA</span></div>
  <nav class="main-nav abs"><span>PRICING</span><span>LEARN MORE</span><span>ABOUT</span><span>TRADE SECRETS</span><span>CONTACT</span></nav>
  <div class="call-btn abs">CALL NOW: 1800 555 019</div>
  <div class="login abs">LOGIN / CREATE ACCOUNT</div>
</header>

<section class="hero abs">
  <div class="skyline abs" style="top:374px" role="img" aria-label="Pale illustrated city skyline with houses and trees"></div>
  <h1 class="hero-title abs" style="top:112px">1000's of Skips at Your Finger Tips</h1>
  <p class="hero-sub abs" style="top:186px">Best Service &amp; Price | Hassle Free | Australia Wide</p>
  <p class="quote-label abs" style="top:252px">Instant Quote</p>
  <div class="search">
    <div class="search-input">Enter postcode or suburb</div>
    <div class="search-btn"><svg width="14" height="14" viewBox="0 0 14 14"><circle cx="6" cy="6" r="4.5" fill="none" stroke="#fff" stroke-width="2"/><line x1="9.5" y1="9.5" x2="13" y2="13" stroke="#fff" stroke-width="2"/></svg>SEARCH</div>
  </div>
</section>

<div class="audience abs">
  <div class="audience-card"><svg width="44" height="44" viewBox="0 0 44 44" fill="none" stroke="#262a63" stroke-width="2"><path d="M6 22 22 8l16 14"/><path d="M11 18v20h22V18"/><rect x="18" y="26" width="8" height="12"/></svg>RENOVATOR</div>
  <div class="audience-card"><svg width="44" height="44" viewBox="0 0 44 44" fill="none" stroke="#262a63" stroke-width="2"><path d="M10 36 26 20"/><circle cx="30" cy="14" r="7"/><path d="M14 8l6 6-4 4-6-6z"/><path d="M24 28l10 10"/></svg>TRADIE</div>
  <div class="audience-card"><svg width="44" height="44" viewBox="0 0 44 44" fill="none" stroke="#262a63" stroke-width="2"><rect x="6" y="10" width="28" height="26"/><path d="M12 30l16-14M28 16h-6M28 16v6"/><path d="M36 6v32"/></svg>BUILDER</div>
  <div class="audience-card"><svg width="44" height="44" viewBox="0 0 44 44" fill="none" stroke="#262a63" stroke-width="2"><rect x="6" y="14" width="32" height="22" rx="2"/><path d="M16 14v-5h12v5M6 23h32"/></svg>CORPORATE</div>
  <div class="audience-card"><svg width="44" height="44" viewBox="0 0 44 44" fill="none" stroke="#262a63" stroke-width="2"><rect x="8" y="8" width="28" height="30"/><path d="M14 14h4M26 14h4M14 21h4M26 21h4M14 28h4M26 28h4"/></svg>NATIONAL</div>
</div>

<h2 class="rated abs">Australia's Highest Rated Skip Bin<br>Hire Company - Rated by You</h2>

<div class="video abs" role="img" aria-label="Animated video still: a man beside a house wondering where his skip bin is"></div>
<div class="play abs"><svg width="26" height="28" viewBox="0 0 26 28"><path d="M4 2 24 14 4 26Z" fill="#262a63"/></svg></div>

<div class="steps-band abs"></div>
<h2 class="section-title abs" style="top:1390px">As Easy As 1, 2, 3...</h2>
<div class="steps abs">
  <div class="step">
    <svg width="54" height="54" viewBox="0 0 54 54" fill="none" stroke="#3a9d5a" stroke-width="2.2"><rect x="4" y="6" width="32" height="24" rx="3"/><path d="M12 30v8l8-8"/><rect x="22" y="22" width="28" height="20" rx="3"/><path d="M42 42v7l-7-7"/></svg>
    <span class="step-num">1</span>
    <h3>Simple, Easy Booking</h3>
    <p>Call <b>1800 555 019</b> or <span>click here</span> to get started with your instant quote</p>
  </div>
  <div class="step">
    <svg width="54" height="54" viewBox="0 0 54 54" fill="none" stroke="#3a9d5a" stroke-width="2.2"><rect x="6" y="4" width="30" height="40" rx="2"/><path d="M12 14h18M12 22h18M12 30h10"/><circle cx="38" cy="38" r="11"/><path d="M33 38l4 4 7-8"/></svg>
    <span class="step-num">2</span>
    <h3>Instant Confirmation</h3>
    <p>Receive your booking details and a 30 minute courtesy call before drop off</p>
  </div>
  <div class="step">
    <svg width="54" height="54" viewBox="0 0 54 54" fill="none" stroke="#3a9d5a" stroke-width="2.2"><path d="M8 20l19-9 19 9-19 9z"/><path d="M8 20v20l19 9 19-9V20M27 29v20"/></svg>
    <span class="step-num">3</span>
    <h3>Gone When Your Ready!</h3>
    <p>Let us know and your bin will be gone within 24hrs</p>
  </div>
</div>
<p class="manage abs">We manage your booking from start to finish,<br>so you can focus on other things</p>

<section class="reviews-band abs"></section>
<h2 class="section-title abs" style="top:1892px">Five Star Service</h2>
<div class="reviews abs">
  <article class="review"><span class="quote-mark">&ldquo;</span><p>There are many variations of passages of available but the majority have suffer alteration in some form by inject humour or random words which don't look even slightly believe you are going middle of text.</p><hr><div class="reviewer"><span class="avatar"></span>Dale Finch</div></article>
  <article class="review"><span class="quote-mark">&ldquo;</span><p>There are many variations of passages of available but the majority have suffer alteration in some form by inject humour or random words which don't look even slightly believe you are going middle of text.</p><hr><div class="reviewer"><span class="avatar"></span>Maren Holt</div></article>
  <article class="review"><span class="quote-mark">&ldquo;</span><p>There are many variations of passages of available but the majority have suffer alteration in some form by inject humour or random words which don't look even slightly believe you are going middle of text.</p><hr><div class="reviewer"><span class="avatar"></span>Reid Calloway</div></article>
</div>
<div class="dots abs"><i></i><i></i><i></i></div>

<h2 class="section-title abs" style="top:2552px">Save Time. Save Money.</h2>
<div class="benefits abs">
  <div class="benefit"><svg width="70" height="48" viewBox="0 0 70 48" fill="none" stroke="#5c5f9f" stroke-width="2.4"><rect x="4" y="14" width="38" height="22"/><path d="M42 20h14l10 10v6H42"/><circle cx="16" cy="40" r="5" fill="#fff"/><circle cx="54" cy="40" r="5" fill="#fff"/><circle cx="20" cy="12" r="9" fill="#fff"/><path d="M20 7v5h4"/></svg><h4>Any Bin, Anytime, Anywhere</h4><p>We connect you with local companies Australia wide; for faster response times, less km's and emissions, greater reliability and lower prices</p></div>
  <div class="benefit"><svg width="48" height="48" viewBox="0 0 48 48" fill="#5c5f9f"><circle cx="24" cy="16" r="10"/><path d="M6 46c0-11 8-18 18-18s18 7 18 18z"/><path d="M12 18c0-8 5-14 12-14s12 6 12 14" fill="none" stroke="#5c5f9f" stroke-width="2.4"/></svg><h4>Service Guaranteed</h4><p>Want to speak to someone when it suits you? We answer the phones and return calls from 7.30am to 8pm 7 days a week</p></div>
  <div class="benefit"><svg width="56" height="48" viewBox="0 0 56 48" fill="none" stroke="#5c5f9f" stroke-width="2.4"><circle cx="34" cy="14" r="10"/><path d="M34 8v12M31 11h5"/><path d="M4 36h12l10 4h14l12-8" /><path d="M16 30h12l6 4"/></svg><h4>Best Pricing</h4><p>We've done the hard work behind the scenes, so with one click you have your best priced, local skip</p></div>
  <div class="benefit"><svg width="56" height="48" viewBox="0 0 56 48" fill="none" stroke="#5c5f9f" stroke-width="2.4"><path d="M4 22l10-8 12 6 10-6 16 8"/><path d="M14 26l10 10c2 2 5 2 7 0l10-10"/><path d="M28 4v6M18 6l3 5M38 6l-3 5"/></svg><h4>First Class Supply Partners</h4><p>Our local supply partners are the best in the business and share our passion for making you happy</p></div>
</div>

<section class="cta abs">
  <div class="search">
    <div class="search-input">Enter postcode or suburb</div>
    <div class="search-btn"><svg width="14" height="14" viewBox="0 0 14 14"><circle cx="6" cy="6" r="4.5" fill="none" stroke="#fff" stroke-width="2"/><line x1="9.5" y1="9.5" x2="13" y2="13" stroke="#fff" stroke-width="2"/></svg>SEARCH</div>
  </div>
</section>
<div class="cta-city abs" role="img" aria-label="Faint city building silhouettes"></div>
<h2 class="cta-title abs">We're ready to go!</h2>
<p class="cta-sub abs">To book, ask questions or just for a chat, call us 7 days a week, 7.30am to 8pm</p>
<p class="cta-label abs">QUICK QUOTE</p>

<footer class="footer abs"></footer>
<ul class="foot-col abs" style="left:117px;list-style:none">
  <li>Skip Bin Hire - Australia Wide</li><li>Sydney</li><li>Melbourne</li><li>Brisbane</li><li>Perth</li><li>Adelaide</li><li>Canberra</li>
</ul>
<ul class="foot-col abs" style="left:445px;list-style:none">
  <li>Learn More</li><li>Waste Types</li><li>Skip Bin Sizes</li><li>Refund Policy</li><li>Pay Later with Paysplit</li><li>FAQ</li><li>Privacy</li>
</ul>
<div class="news abs" style="left:717px;top:3292px;padding-top:0">
  <div style="margin-top:0"></div>
</div>
<div class="news abs" style="left:717px;top:3292px">
  <h5 style="margin-top:0"> </h5>
</div>
<div class="news abs" style="left:717px;top:3290px;"></div>
<div class="news abs" style="left:717px;top:3300px"></div>
<div class="news abs" style="left:717px;top:3304px"></div>
<div class="news abs" style="left:717px;top:3304px"></div>
<div class="news abs" style="left:717px;top:3302px"></div>
<div class="news abs" style="left:717px;top:3302px"></div>
<div class="news abs" style="left:717px;top:3408px">
  <h5>Latest Industry News</h5>
  <p>Sign up for the latest news, offers from<br>TALLOW CRATE RENTALS AUSTRALIA</p>
  <div class="subscribe"><span>Your email</span><b>SUBSCRIBE</b></div>
  <div class="social"><i></i><i></i><i></i><i></i></div>
</div>

<div class="base abs"></div>
<p class="copyright abs">Copyright © 2019, TALLOW CRATE RENTALS AUSTRALIA. Powered by Cartwell</p>
<div class="pay abs"><i></i><i></i><i></i><i></i><i></i></div>

</body>
</html>
```